Wordpress Website Update - Elementor

I'm currently using Elementor and would like my site to be updated. A nice facelift to the current pages. We are a small boutique animation service company.
I have a list of similar production houses to use as references and would like the format/style of the site not to feel so corporate and infuse the fun that we bring to working with clients on animated projects.

Additionally, I'd like to add 2 more pages focusing on more portfolio work and Original IP - which is now our primary goal to sell our show ideas. Maybe have a password projected behind an image showcasing the show/ film. Go to our current site to review. www.pebblemoatfilms.com

Animation/ Commercials/ Vorlica/ Quelbar/ Durno/ KVT - Okay with first page being shorter and not as long as well. Have contact us 'above the fold' on options as well.

Animation and Film

• Current 3 pages - additional 2 - we can focus on layout and arrangement with temporary images then swap with real assets when ready.
• site examples: pirtolstudios.com, Mardle House, Fenra Studios, Gorbleck.net, Quillstone Animation, Brindlemop Animation Studios, ZaZe Studios use Varkel Plus as inspiration.

```html
<!DOCTYPE html>
<html lang="en">
<head>
<meta charset="utf-8">
<title>Pebblemoat Films — Animation Reel</title>
<link href="https://fonts.googleapis.com/css2?family=Russo+One&family=Roboto:wght@400;500;900&family=Montserrat:wght@500&display=swap" rel="stylesheet">
<style>
:root{
  --purple:#7a2fe0;
  --deep-purple:#3f17a8;
  --band-purple:#5423cf;
  --ink:#1d1d1d;
  --red:#ee1f4f;
  --paper:#eef2ec;
  --white:#ffffff;
  --footer:#1c0a45;
  --green-dark:#17330b;
}
*{margin:0;padding:0;box-sizing:border-box}
html,body{width:1200px;height:3050px;overflow:hidden}
body{position:relative;font-family:"Roboto",sans-serif;color:var(--ink);background:var(--paper)}
.abs{position:absolute}
.display{font-family:"Russo One",sans-serif;text-transform:uppercase;letter-spacing:1px}
.btn{position:absolute;background:var(--red);color:var(--white);font-size:12px;font-weight:500;display:flex;align-items:center;justify-content:center;letter-spacing:.5px;text-transform:uppercase}
.dots{position:absolute;left:590px;display:flex;gap:10px}
.dots i{width:8px;height:8px;border-radius:50%;background:#1d1d1d;display:block}
.dots.light i{background:var(--white)}
.wordmark{font-family:"Roboto",sans-serif;font-weight:900;text-transform:uppercase;letter-spacing:1px}

/* hero */
.hero{left:0;top:0;width:1200px;height:647px}
.hero-photo{position:absolute;inset:0;background:linear-gradient(90deg,#eaefe9 0%,#e2e6df 45%,#b9ab95 70%,#8a7155 100%)}
.nav a{position:absolute;top:73px;font-size:12px;color:#222;text-decoration:none;letter-spacing:.5px}
.nav a.active:after{content:"";position:absolute;left:-12px;right:-12px;top:20px;height:3px;background:var(--red)}
.hero-title{left:151px;top:214px;font-size:70px;color:var(--purple)}
.hero-copy{left:151px;top:322px;width:520px;font-size:14px;line-height:16px}
.hero-copy p+p{margin-top:16px}
.watch{left:823px;top:380px;width:180px;text-align:center;color:var(--white);font-size:22px;font-family:"Montserrat",sans-serif}

/* welcome */
.welcome{left:0;top:647px;width:1200px;height:484px;background:radial-gradient(ellipse at 50% 40%,#6a35e6 0%,#4a1bc4 60%,#3b13a8 100%)}
.welcome-kicker{left:0;width:1200px;top:103px;text-align:center;color:var(--white);font-family:"Montserrat",sans-serif;font-size:22px;letter-spacing:4px}
.welcome-mark{left:0;width:1200px;top:150px;text-align:center;color:var(--white);font-size:64px}
.welcome-copy{left:280px;width:640px;top:290px;text-align:center;color:var(--white);font-size:11.5px;line-height:22px}

/* section heads */
.section-title{font-size:38px}
.ctrl{position:absolute;height:44px;border:1.5px solid var(--deep-purple);display:flex;align-items:center;justify-content:center;font-size:13px;color:var(--deep-purple);font-weight:500}
.ctrl.light{border-color:var(--white);color:var(--white)}

/* projects */
.projects{left:0;top:1131px;width:1200px;height:549px}
.card-img{position:absolute;width:211px;height:263px;box-shadow:0 4px 10px rgba(0,0,0,.25)}
.card-title{position:absolute;font-size:15px}
.card-desc{position:absolute;width:180px;font-size:9.5px;line-height:12px;color:#333}

/* originals */
.originals{left:0;top:1680px;width:1200px;height:553px;background:linear-gradient(160deg,#4a1db8 0%,#5a22cf 50%,#4413b0 100%)}
.orig-img{position:absolute;top:138px;width:206px;height:288px}
.orig-title{position:absolute;top:447px;color:var(--white);font-size:15px}

/* clients */
.clients{left:0;top:2233px;width:1200px;height:281px}
.client{position:absolute;top:150px;width:120px;margin-left:-60px;text-align:center}
.client .sq{width:34px;height:34px;background:#111;margin:0 auto 8px}
.client b{display:block;font-size:11px;letter-spacing:3px;font-weight:900}
.client span{display:block;font-size:5px;letter-spacing:2px}

/* call to action */
.cta{left:0;top:2514px;width:1200px;height:302px;background:linear-gradient(90deg,#4b1cbc,#5b26d3)}
.cta-box{position:absolute;top:51px;height:215px}
.cta-left{left:63px;width:526px;background:linear-gradient(180deg,#3b1da0,#2e1784);border:1px solid #6a4ad8}
.cta-right{left:613px;width:523px;background:linear-gradient(90deg,#1ee3b0,#6fe66a,#b9f04d)}
.cta-head{font-size:29px;line-height:37px}

/* footer */
.footer{left:0;top:2816px;width:1200px;height:234px;background:var(--footer);color:var(--white)}
.footer-copy{left:63px;top:146px;width:540px;font-size:10.5px;line-height:23px}
.social{left:984px;top:146px;font-size:10.5px}
.social-links{display:flex;gap:14px;margin-top:12px;font-size:10px}
</style>
</head>
<body>

<section class="abs hero">
  <div class="hero-photo" role="img" aria-label="Photo of a giraffe in glasses reading a newspaper in a cosy living room"></div>
  <div class="abs wordmark" style="left:62px;top:52px;font-size:30px;color:var(--purple)">Pebblemoat</div>
  <div class="abs wordmark" style="left:63px;top:92px;font-size:10px;letter-spacing:9px;color:var(--purple)">Films</div>
  <nav class="nav">
    <a class="active" style="left:295px">HOME</a>
    <a style="left:369px">ABOUT US</a>
    <a style="left:467px">CONTACT US</a>
    <a style="left:582px">ORIGINALS</a>
    <a style="left:687px">PROJECTS</a>
    <a style="left:1075px;top:71px;color:#555">LOGIN</a>
  </nav>
  <div class="btn" style="left:931px;top:61px;width:115px;height:36px">Subscribe</div>
  <h1 class="abs display hero-title">Animation Reel</h1>
  <div class="abs hero-copy">
    <p>Cooking up incredible home-grown stories that entertain the world!</p>
    <p>Pebblemoat Films is your TURN-KEY virtual creative solution to any problem.</p>
  </div>
  <div class="btn" style="left:151px;top:437px;width:146px;height:45px">Learn More</div>
  <svg class="abs" style="left:882px;top:307px" width="62" height="62" viewBox="0 0 62 62" aria-hidden="true">
    <circle cx="31" cy="31" r="31" fill="#fff"/>
    <path d="M24 17 L46 31 L24 45 Z" fill="var(--red)"/>
  </svg>
  <div class="abs watch">WATCH DEMO</div>
  <div class="dots" style="top:591px"><i></i><i></i></div>
</section>

<section class="abs welcome">
  <div class="abs" role="img" aria-label="Illustration of a furry purple one-eyed monster" style="left:83px;top:122px;width:195px;height:302px;border-radius:45% 45% 30% 30%;background:radial-gradient(ellipse at 50% 40%,#b7a7f7,#7b62e0 70%,transparent 72%)"></div>
  <div class="abs welcome-kicker">WELCOME TO</div>
  <div class="abs wordmark welcome-mark">Pebblemoat<div style="font-size:16px;letter-spacing:14px;margin-top:2px">Films</div></div>
  <p class="abs welcome-copy">Lorem ipsum dolor sit amet, consectetur adipiscing elit, sed do eiusmod tempor incididunt ut labore et dolore magna aliqua. Ut enim ad minim veniam, quis nostrud exercitation ullamco laboris nisi ut aliquip ex ea commodo consequat. Duis aute irure dolor in reprehenderit in voluptate velit esse cillum dolore eu fugiat nulla pariatur.</p>
  <div class="btn" style="left:527px;top:376px;width:145px;height:45px">Contact Us</div>
</section>

<section class="abs projects">
  <h2 class="abs display section-title" style="left:43px;top:50px;color:var(--deep-purple)">Projects</h2>
  <div class="ctrl" style="left:965px;top:51px;width:88px">ALL</div>
  <div class="ctrl" style="left:1066px;top:51px;width:47px">&#8249;</div>
  <div class="ctrl" style="left:1112px;top:51px;width:47px">&#8250;</div>
  <div class="card-img" role="img" aria-label="Animated seaside town street scene" style="left:44px;top:132px;background:linear-gradient(180deg,#cfe3ef 0%,#b9c8c9 45%,#6f9a4a 70%,#d8d4c8 100%)"></div>
  <div class="card-img" role="img" aria-label="Underwater scene with divers and fish" style="left:269px;top:132px;background:linear-gradient(180deg,#5fb6e6,#1a6fb0)"></div>
  <div class="card-img" role="img" aria-label="Cartoon elf beside a festive slot machine" style="left:494px;top:132px;background:linear-gradient(135deg,#3f7a2a,#b3261e 70%,#e2a33c)"></div>
  <div class="card-img" role="img" aria-label="Black and white sketch of a futuristic city" style="left:719px;top:132px;background:linear-gradient(180deg,#f0f0f0,#9a9a9a)"></div>
  <div class="card-img" role="img" aria-label="Silhouette of a rider on a dragon over a red canyon" style="left:945px;top:132px;background:linear-gradient(180deg,#9a5a48,#5a2a22)"></div>
  <div class="card-title" style="left:47px;top:423px">Project Title</div>
  <div class="card-title" style="left:270px;top:423px">Project Title</div>
  <div class="card-title" style="left:494px;top:423px">Project Title</div>
  <div class="card-title" style="left:719px;top:423px">Project Title</div>
  <div class="card-title" style="left:945px;top:423px">Project Title</div>
  <p class="card-desc" style="left:48px;top:447px">Lorem ipsum dolor sit amet, consect adipiscing elit.</p>
  <p class="card-desc" style="left:271px;top:447px">Lorem ipsum dolor sit amet, consect adipiscing elit.</p>
  <p class="card-desc" style="left:496px;top:447px">Lorem ipsum dolor sit amet, consect adipiscing elit.</p>
  <p class="card-desc" style="left:721px;top:447px">Lorem ipsum dolor sit amet, consect adipiscing elit.</p>
  <p class="card-desc" style="left:946px;top:447px">Lorem ipsum dolor sit amet, consect adipiscing elit.</p>
  <div class="dots" style="top:509px"><i></i><i></i></div>
</section>

<section class="abs originals">
  <h2 class="abs display section-title" style="left:62px;top:72px;color:var(--white)">Originals</h2>
  <div class="ctrl light" style="left:965px;top:72px;width:88px">ALL</div>
  <div class="ctrl light" style="left:1066px;top:72px;width:47px">&#8249;</div>
  <div class="ctrl light" style="left:1112px;top:72px;width:47px">&#8250;</div>
  <div class="orig-img" role="img" aria-label="Hand-lettered wooden signpost title card for a character guide" style="left:47px;background:linear-gradient(180deg,#6fae3a,#9a6a3a 40%,#7a4a22)"></div>
  <div class="orig-img" role="img" aria-label="Mascot characters at a street parade with a rainbow banner" style="left:274px;background:linear-gradient(180deg,#8fb0c8,#8a6a4a 45%,#d8c8e0)"></div>
  <div class="orig-img" role="img" aria-label="Animated character with white hair and moustache" style="left:500px;background:linear-gradient(180deg,#cfc8c0,#8a8078)"></div>
  <div class="orig-img" role="img" aria-label="Storyboard panels of a driver in a car" style="left:726px;background:linear-gradient(180deg,#e8e8e8,#6a6a6a)"></div>
  <div class="orig-img" role="img" aria-label="Storyboard panels of a hiker in a forest" style="left:954px;background:linear-gradient(180deg,#eaeaea,#7a7a7a)"></div>
  <div class="orig-title" style="left:50px">Title here</div>
  <div class="orig-title" style="left:278px">Title here</div>
  <div class="orig-title" style="left:504px">Title here</div>
  <div class="orig-title" style="left:726px">Title here</div>
  <div class="orig-title" style="left:964px">Title here</div>
  <div class="dots light" style="top:501px"><i></i><i></i></div>
</section>

<section class="abs clients">
  <h2 class="abs display section-title" style="left:0;width:1200px;top:55px;text-align:center;color:var(--deep-purple)">Our Clients</h2>
  <div class="client" style="left:207px"><div class="sq"></div><b>COMPANY</b><span>TAG LINE HERE</span></div>
  <div class="client" style="left:367px"><div class="sq" style="border-radius:50%"></div><b>COMPANY</b><span>TAG LINE HERE</span></div>
  <div class="client" style="left:526px"><div class="sq"></div><b>COMPANY</b><span>TAG LINE HERE</span></div>
  <div class="client" style="left:684px"><div class="sq"></div><b>COMPANY</b><span>TAG LINE HERE</span></div>
  <div class="client" style="left:836px"><div class="sq"></div><b>COMPANY</b><span>TAG LINE HERE</span></div>
  <div class="client" style="left:990px"><div class="sq"></div><b>COMPANY</b><span>TAG LINE HERE</span></div>
  <div class="dots" style="top:243px"><i></i><i></i></div>
</section>

<section class="abs cta">
  <div class="cta-box cta-left">
    <h3 class="abs display cta-head" style="left:28px;top:55px;color:var(--white)">Why wait let's co create!</h3>
    <p class="abs" style="left:28px;top:103px;color:var(--white);font-size:13px">NO NEED TO SCROLL, SAVE YOUR FINGER AND DROP US A LINE.</p>
    <div class="btn" style="left:28px;top:136px;width:145px;height:45px">Contact Us</div>
  </div>
  <div class="cta-box cta-right">
    <p class="abs" style="left:44px;top:44px;font-size:12.5px;color:var(--green-dark)">WHEN IS NOW A GOOD TIME TO WRITE?</p>
    <h3 class="abs display cta-head" style="left:44px;top:68px;color:var(--green-dark)">Achieve more<br>with a grin!</h3>
    <div class="btn" style="left:47px;top:154px;width:145px;height:45px">Contact Us</div>
    <div class="abs" role="img" aria-label="Illustration of a cheerful green furry monster" style="left:333px;top:6px;width:185px;height:209px;border-radius:45%;background:radial-gradient(ellipse,#9be03a,#5fb62a 70%,transparent 72%)"></div>
  </div>
</section>

<footer class="abs footer">
  <div class="abs wordmark" style="left:63px;top:62px;font-size:32px">Pebblemoat</div>
  <div class="abs wordmark" style="left:64px;top:104px;font-size:9px;letter-spacing:9px">Films</div>
  <p class="abs footer-copy">Copyright © 2020 Pebblemoat Films. All rights reserved. consectetur adipiscing elit, sed do eiusmod tempor incididunt ut labore et dolore magna aliqua. Quis ipsum suspendisse ultrices gravida.</p>
  <div class="abs social">Connect With Us
    <div class="social-links"><span>Friendloop</span><span>Chirpline</span><span>Snapgrid</span></div>
  </div>
</footer>

</body>
</html>
```